Business Card Design for Marketing Firm

Looking for business card design for higher end marketing firm. Clean but impressionable/trendy. We are a marketing firm that represents manufacturers in the foodservice equipment and supply industry. Our customers are end users such has hotels, restaurants, country clubs, convention centers and casinos as well as distributors of restaurants supplies and equipment, and manufacturers of foodservice equipment and supplies.
Target Market(s)
Hotels, Restaurants, Supply & Equipment Distributors, Foodservice Manufacturers
Industry/Entity Type
Foodservice/Hospitality
Contact Information for Business Card
Name, Title, Contact Number, Email, Website, Social Media, Address
Requirements
Must have
- Clean & Simple but Serious and Impressionable

```html
<!DOCTYPE html>
<html lang="en">
<head>
<meta charset="utf-8">
<title>Meridian Service Reps — Business Card</title>
<link href="https://fonts.googleapis.com/css2?family=Montserrat:wght@400;600;700&display=swap" rel="stylesheet">
<style>
  :root {
    --navy: #28245a;
    --navy-deep: #1c1940;
    --ink: #2b2a33;
    --muted: #4a4a52;
    --rule: #2b2a40;
    --band-grey: #b9b9bd;
    --card: #ffffff;
    --backdrop: #e8e5df;
    --pattern-light: #b4b0cc;
    --pattern-dark: #14122e;
  }
  * { box-sizing: border-box; margin: 0; padding: 0; }
  html, body { width: 900px; height: 1200px; overflow: hidden; }
  body {
    background: var(--backdrop);
    font-family: "Montserrat", Arial, sans-serif;
    position: relative;
  }
  .card {
    position: absolute;
    left: 80px;
    width: 742px;
    height: 440px;
    border-radius: 30px;
    overflow: hidden;
  }
  .card--front { top: 132px; background: var(--card); }
  .card--back  { top: 638px; background: var(--navy); }

  .brand-name {
    position: absolute;
    left: 42px;
    top: 150px;
    font-size: 30px;
    font-weight: 600;
    letter-spacing: 1.5px;
    color: var(--navy);
    line-height: 1.2;
  }

  .person { position: absolute; right: 44px; top: 279px; text-align: right; }
  .person__name { font-size: 26px; font-weight: 700; color: var(--navy); line-height: 1.1; }
  .person__title { font-size: 15px; font-weight: 400; color: var(--muted); margin-top: 9px; }

  .divider {
    position: absolute;
    left: 42px;
    top: 324px;
    width: 506px;
    height: 1.5px;
    background: var(--rule);
  }

  .contacts { position: absolute; left: 38px; top: 342px; list-style: none; }
  .contacts__item {
    display: flex;
    align-items: center;
    gap: 12px;
    height: 24px;
    font-size: 16px;
    color: var(--ink);
  }
  .contacts__icon { width: 14px; height: 14px; fill: var(--ink); flex: none; }

  .bands { position: absolute; left: 0; top: 0; width: 742px; height: 440px; }

  .address {
    position: absolute;
    right: 30px;
    top: 412px;
    font-size: 16px;
    color: #ffffff;
  }

  .monogram-pattern {
    position: absolute;
    inset: 0;
    background:
      linear-gradient(90deg, rgba(180,176,204,0.55) 0%, rgba(120,116,150,0.35) 35%, rgba(20,18,46,0.55) 70%, rgba(20,18,46,0.7) 100%),
      var(--navy);
  }
</style>
</head>
<body>

  <section class="card card--front" aria-label="Business card front">
    <svg class="bands" viewBox="0 0 742 440" aria-hidden="true">
      <polygon points="0,424 318,424 306,440 0,440" fill="var(--band-grey)"/>
      <polygon points="352,400 742,400 742,440 318,440" fill="var(--navy)"/>
    </svg>

    <div class="brand-name">MERIDIAN SERVICE REPS</div>

    <div class="person">
      <div class="person__name">Daniel Reyes</div>
      <div class="person__title">CEO &amp; Founder</div>
    </div>

    <div class="divider"></div>

    <ul class="contacts">
      <li class="contacts__item">
        <svg class="contacts__icon" viewBox="0 0 24 24" aria-hidden="true"><path d="M6.6 10.8a15.1 15.1 0 0 0 6.6 6.6l2.2-2.2a1 1 0 0 1 1-.25 11.4 11.4 0 0 0 3.6.57 1 1 0 0 1 1 1V20a1 1 0 0 1-1 1A17 17 0 0 1 3 4a1 1 0 0 1 1-1h3.5a1 1 0 0 1 1 1c0 1.25.2 2.45.57 3.57a1 1 0 0 1-.25 1z"/></svg>
        <span>(555) 014-2290</span>
      </li>
      <li class="contacts__item">
        <svg class="contacts__icon" viewBox="0 0 24 24" aria-hidden="true"><path d="M2 5h20v14H2z M2 5l10 8 10-8" fill="var(--ink)"/><path d="M3 6l9 7 9-7" stroke="#fff" stroke-width="1.6" fill="none"/></svg>
        <span>info@meridianservicereps.com</span>
      </li>
      <li class="contacts__item">
        <svg class="contacts__icon" viewBox="0 0 24 24" aria-hidden="true"><circle cx="12" cy="12" r="10"/><path d="M2 12h20M12 2c3 3 3 17 0 20M12 2c-3 3-3 17 0 20" stroke="#fff" stroke-width="1.4" fill="none"/></svg>
        <span>www.meridianservicereps.com</span>
      </li>
    </ul>

    <div class="address">240 Harbor Lane, Suite 900, Bayview, CA 90210</div>
  </section>

  <section class="card card--back" aria-label="Business card back">
    <div class="monogram-pattern" role="img" aria-label="Repeating brand monogram pattern fading from silver to black across a navy field"></div>
  </section>

</body>
</html>
```